Brightmoor - a website to encourage people to spend time in nature

I have a squarespace site with some content on it but the squarespace template doesn't completely suit my needs, I keep fiddling with the template but actually I need some professional help to get it looking the way I want and with the right 'mood'.
The website is for "Brightmoor" - it will be a blog where I write about the importance of nature for good health. I also want to use the website to market services such as outdoor coaching, retreats and walking workshops.
This has been in my head for a LONG time and I currently only use instagram for micro-blogs but it's time for me to get this moving. I've previously engaged other designers on branding for it but they just didn't get it quite the way that I wanted it and I wasn't completely happy with the results. It's been a process for me as to what I want but in the meantime I just didn't come back to the design aspect of it now. I'm looking for a designer who understands the purpose of the website, the ethos and can help me realise this into a design that's clean, clear and simple.

Please note that I have a domain (brightmoor.org) and a lot of content drafted on squarespace already. I have published it with password protection - password is brightmoor2020 - it still has some of the original template on it, but does have some content. Don't take it as anything to follow in particular, i am looking for fresh eyes and fresh ideas.

Target Market(s)

There are three main groups that I want to target - people who are suffering from stress and anxiety, people who treat them and parents who want to get their kids outside (thereby preventing stress and anxiety)

Contact Information for Business Card

Joan Petrie
Brightmoor
Telephone +44 7700 900417
brightmoor@mailvane.com

Logo Text

Brightmoor - if that. I have an idea that the logo should have a leaf on it somewhere, or maybe just be a leaf.

Coding

Coded - Design and coding required

Number of Pages Required

5+ page

Font styles to use
Serif
Sans Serif

Colors
add136
33b8a4
34a6d7
3377b5

Requirements
Must have
• Space for lots of images. The ability for me to edit the pages if I need to. Be user friendly. Look beautiful.
• For an idea of the images I use and the content I'm interested in writing about have a look at @brightmoor on instagram.
• That pop up about cookies so I am complying with data laws.
Should not have
• Must not be too 'busy' I'd like to avoid too much movement.

```html
<!DOCTYPE html>
<html lang="en">
<head>
<meta charset="utf-8">
<title>Brightmoor – Business Card</title>
<link rel="stylesheet" href="https://fonts.googleapis.com/css2?family=Noticia+Text:wght@700&family=Poppins:wght@400&display=swap">
<style>
  :root {
    --backdrop: #e9ebea;
    --paper: #fbfbf9;
    --teal: #3db9a6;
    --teal-deep: #1f7f73;
    --teal-ink: #17695f;
    --leaf: #add136;
    --leaf-pale: #eef3d6;
    --mint-pale: #d9f0ea;
    --white: #ffffff;
  }
  * { box-sizing: border-box; margin: 0; padding: 0; }
  html, body {
    width: 1200px; height: 1200px; overflow: hidden;
    background: var(--backdrop);
  }
  .sheet {
    width: 1200px; height: 1200px;
    display: flex; flex-direction: column; align-items: center; justify-content: center;
    gap: 60px;
  }
  .card {
    position: relative;
    width: 840px; height: 480px;
    overflow: hidden;
    box-shadow: 0 10px 30px rgba(0,0,0,0.12);
  }

  /* Front */
  .card--front { background: var(--paper); }
  .front__foliage {
    position: absolute;
    border-radius: 50%;
  }
  .front__foliage--left {
    left: -60px; top: 40px; width: 300px; height: 440px;
    background: radial-gradient(ellipse at center, var(--leaf-pale) 0%, var(--mint-pale) 45%, rgba(251,251,249,0) 72%);
  }
  .front__foliage--right {
    right: -70px; bottom: -60px; width: 320px; height: 420px;
    background: radial-gradient(ellipse at center, var(--leaf-pale) 0%, var(--mint-pale) 45%, rgba(251,251,249,0) 72%);
  }
  .brand {
    position: absolute; inset: 0;
    display: flex; flex-direction: column; align-items: center; justify-content: center;
    gap: 18px;
  }
  .brand__name {
    font-family: "Noticia Text", Georgia, serif;
    font-weight: 700;
    font-size: 76px;
    color: var(--teal);
    letter-spacing: 1px;
  }
  .brand__url {
    font-family: "Poppins", Arial, sans-serif;
    font-size: 22px;
    letter-spacing: 3px;
    color: var(--teal-deep);
  }

  /* Back */
  .card--back { background: var(--teal); }
  .back__foliage {
    position: absolute;
    left: -40px; top: -80px; width: 640px; height: 380px;
    border-radius: 50%;
    background: radial-gradient(ellipse at 45% 50%, rgba(173,209,54,0.55) 0%, rgba(173,209,54,0.25) 40%, rgba(61,185,166,0) 70%);
  }
  .contact {
    position: absolute;
    right: 70px; bottom: 70px;
    text-align: right;
  }
  .contact__name {
    font-family: "Noticia Text", Georgia, serif;
    font-weight: 700;
    font-size: 54px;
    color: var(--white);
    letter-spacing: 1px;
    margin-bottom: 22px;
  }
  .contact__line {
    font-family: "Poppins", Arial, sans-serif;
    font-size: 26px;
    line-height: 1.45;
    color: var(--teal-ink);
  }
</style>
</head>
<body>
  <main class="sheet">
    <section class="card card--front">
      <div class="front__foliage front__foliage--left" role="img" aria-label="Soft swirling vine with pale leaves"></div>
      <div class="front__foliage front__foliage--right" role="img" aria-label="Soft swirling vine with pale leaves"></div>
      <div class="brand">
        <div class="brand__name">Brightmoor</div>
        <div class="brand__url">www.brightmoor.org</div>
      </div>
    </section>

    <section class="card card--back">
      <div class="back__foliage" role="img" aria-label="White curling vine with green leaves"></div>
      <div class="contact">
        <div class="contact__name">Joan Petrie</div>
        <div class="contact__line">+44 7700 900417</div>
        <div class="contact__line">brightmoor@mailvane.com</div>
      </div>
    </section>
  </main>
</body>
</html>
```